Website Banner Design Needed for Health/Medical Business

We are looking for a creative and professional set of banners for the front page of our:
1. website - kelvoramedics.com.au and lunetaskin.com.au and bluemoorcare.com.au

then edit the above banners to the corrrect sizes for below
2. Our facebook pages (1 for each of the above websites)

3. Our google + pages (2 in total one for melb and syd)

4. You tube pages (1 for kelvoramedics and 1 for lunetaskin)

We are looking for something fresh and clean that gives the feeling of:
1. Medical (dont show pictures of doctors though - nurses are ok - just not doctors)
2. Modern because PRP is a modern medical procedure
3. Most Experienced - No other clinic in Australia has performed as many PRP treatments compared to us.
4. We offer a 100% money back guarantee as well

The banners will not be animated or using layers. they will be still banners.

We would prefer to use new stock images and will purchase them for you after you have provided some suggestions/initial drafts.

Target Market(s)

men and women from 25-65

Industry/Entity Type

Health And Wellness

Number of Pages Required

1 page

Font styles to use
Sans Serif

Requirements
Must have
• no doctor images
• nurses are ok - but no doctor images
• for the images avoid fake themed images eg. a person looking in the mirror at their hair loss = NO NO NO..... instead aim for a nurse holding a test tube or a clipboard .
• The banners need to emphasise we are the only clinic who has performed 11,000+ treatments in australia
Nice to have
• a medical feeling would be nice - but dont make it too medical. i want the viewer to associate the word TRUSTED PROVEN and RELIABLE when they view the banner.
Should not have
• as mentioned no doctor or images that look like hospital too much.
• we are a private clinic run by nurses - i have to becareful not to mislead the viewer

```html
<!DOCTYPE html>
<html lang="en">
<head>
<meta charset="utf-8">
<title>Reliable &amp; Trusted – PRP Hair Treatment Banner</title>
<link rel="stylesheet" href="https://fonts.googleapis.com/css2?family=Montserrat:wght@500;600;700&family=Oswald:wght@400&family=Great+Vibes&display=swap">
<style>
  :root {
    --page-bg: #ececec;
    --banner-bg: #ffffff;
    --wave-blue: #2a86c8;
    --navy: #1c4f8c;
    --leaf-green: #c6e89a;
    --text-grey: #4a4a4a;
    --photo-light: #ece6e2;
    --photo-mid: #b9b2ad;
    --photo-dark: #6f6a68;
  }
  * { margin: 0; padding: 0; box-sizing: border-box; }
  html, body {
    width: 1200px;
    height: 618px;
    overflow: hidden;
    background: var(--page-bg);
  }
  .stage {
    position: relative;
    width: 1200px;
    height: 618px;
  }
  .banner {
    position: absolute;
    left: 20px;
    top: 112px;
    width: 1276px;
    height: 432px;
    transform: scale(0.9091);
    transform-origin: 0 0;
    background: var(--banner-bg);
    overflow: hidden;
  }
  .banner-art {
    position: absolute;
    inset: 0;
    width: 1276px;
    height: 432px;
  }
  .guarantee-badge {
    position: absolute;
    left: 41px;
    top: 118px;
    width: 164px;
    height: 164px;
    border-radius: 50%;
    background: var(--navy);
    border: 4px solid #ffffff;
    box-shadow: 0 0 0 1px rgba(28, 79, 140, 0.25);
    color: #ffffff;
    font-family: "Montserrat", sans-serif;
    text-align: center;
    display: flex;
    flex-direction: column;
    justify-content: center;
    align-items: center;
    line-height: 1.1;
  }
  .guarantee-badge .percent { font-size: 38px; font-weight: 700; }
  .guarantee-badge .money-back { font-size: 17px; font-weight: 500; margin-top: 2px; }
  .guarantee-badge .guarantee { font-size: 19px; font-weight: 600; margin-top: 2px; }
  .tagline-script {
    position: absolute;
    left: 42px;
    top: 352px;
    font-family: "Great Vibes", cursive;
    font-size: 42px;
    color: var(--navy);
    white-space: nowrap;
  }
  .claim {
    position: absolute;
    right: 44px;
    top: 284px;
    text-align: right;
    font-family: "Montserrat", sans-serif;
    color: var(--text-grey);
  }
  .claim .claim-lead { font-size: 16.5px; font-weight: 500; letter-spacing: 0.2px; }
  .claim .claim-figure { font-size: 22px; font-weight: 700; margin-top: 1px; letter-spacing: 0.3px; }
  .headline {
    position: absolute;
    right: 42px;
    top: 334px;
    font-family: "Oswald", sans-serif;
    font-weight: 400;
    font-size: 50px;
    line-height: 1.1;
    color: var(--navy);
    white-space: nowrap;
    letter-spacing: -0.5px;
  }
</style>
</head>
<body>
<div class="stage">
  <section class="banner">
    <svg class="banner-art" viewBox="0 0 1276 432" xmlns="http://www.w3.org/2000/svg">
      <defs>
        <linearGradient id="photoTone" x1="0" y1="0" x2="1" y2="0">
          <stop offset="0" stop-color="var(--photo-dark)"/>
          <stop offset="0.3" stop-color="var(--photo-mid)"/>
          <stop offset="0.7" stop-color="var(--photo-light)"/>
          <stop offset="1" stop-color="#ffffff"/>
        </linearGradient>
      </defs>
      <path role="img" aria-label="Photo: a smiling nurse caring for an elderly woman in a bright room"
            fill="url(#photoTone)"
            d="M0,60 C150,270 300,390 520,350 C760,305 900,160 1005,110 V0 H0 Z"/>
      <path class="wave-band" fill="var(--wave-blue)"
            d="M0,55 C150,260 300,380 520,340 C800,290 1000,40 1276,25
               L1276,70 C1010,85 830,330 520,372 C320,400 170,330 0,112 Z"/>
      <path class="wave-line-navy" fill="none" stroke="var(--navy)" stroke-width="3"
            d="M0,168 C120,330 300,410 500,396 C760,375 930,170 1100,155 C1180,150 1240,180 1276,198"/>
      <path class="wave-line-green" fill="none" stroke="var(--leaf-green)" stroke-width="3"
            d="M420,398 C700,380 900,170 1075,163 C1160,160 1230,215 1276,262"/>
    </svg>

    <div class="guarantee-badge">
      <span class="percent">100%</span>
      <span class="money-back">Money Back</span>
      <span class="guarantee">Guarantee</span>
    </div>

    <p class="tagline-script">Reliable &amp; Trusted</p>

    <div class="claim">
      <p class="claim-lead">Only Australian clinic to perform</p>
      <p class="claim-figure">11,000+ PRP treatments</p>
    </div>

    <h1 class="headline">Loosing Your Hair is a Choice</h1>
  </section>
</div>
</body>
</html>
```